Webdesign für Hersteller für Pack- und Palettieranlagen für den Getränke- und Lebensmittelbereich
Webdesign für Hersteller für Pack- und Palettieranlagen für den Getränke- und Lebensmittelbere..
Zielgruppe
Hersteller für Pack- und Palettieranlagen für den Getränke- und Lebensmittelbereich
Zielgruppe: Getränke- und Lebensmittelhersteller
Aufgabenstellung
die zukünftige Seite soll dynamischer und intuitiver werden
klare Strukturen, aber morderner als das jetztige Layout
Keine Kopie der alten Seite www.kolmatech.de!
Startseite soll aufgeräumter sein
Logo, Rufnummer, Mail, Social Media
Startseite mit großem Headerbild (Slider)

```html
<!DOCTYPE html>
<html lang="de">
<head>
<meta charset="utf-8">
<title>KOLMATECH Maschinenbau GmbH</title>
<link href="https://fonts.googleapis.com/css2?family=Montserrat:ital,wght@0,300;0,400;0,500;0,600;0,700;0,800;0,900;1,300&display=swap" rel="stylesheet">
<style>
:root{
  --green:#6cb33f;
  --green-dark:#5a9c30;
  --orange:#f29a38;
  --ink:#1d1d1d;
  --grey-text:#555;
  --light:#eef1f3;
  --footer:#1c1d1f;
}
*{box-sizing:border-box;margin:0;padding:0}
html,body{width:1200px;height:4367px;overflow:hidden}
body{font-family:'Montserrat',sans-serif;color:var(--ink);background:#fff;position:relative}
.abs{position:absolute}
.btn{position:absolute;display:flex;align-items:center;justify-content:center;background:var(--green);color:#fff;font-weight:700;text-transform:uppercase;letter-spacing:.5px}
.ph{position:absolute}

/* header */
.topbar{position:absolute;left:0;top:0;width:1200px;height:81px;background:#fff}
.brand{position:absolute;left:97px;top:14px;display:flex;align-items:center;gap:10px}
.brand-dot{width:34px;height:34px;border-radius:50%;background:var(--green)}
.brand-name{font-weight:800;font-size:32px;color:var(--green);line-height:1}
.brand-sub{font-size:15px;font-weight:600;color:#333;margin-top:3px}
.contact{position:absolute;top:31px;display:flex;align-items:center;gap:10px;font-size:14px;font-weight:500}
.kontakt{left:1010px;top:25px;width:88px;height:35px;font-size:13px;border:2px solid #c5e1b0}
.nav{position:absolute;left:0;top:81px;width:1200px;height:58px;background:var(--green);display:flex;align-items:center;padding-left:97px;gap:0}
.nav a{color:#fff;font-size:14px;font-weight:700;text-decoration:none;padding:0 11px;height:58px;display:flex;align-items:center}
.nav a.active{background:#fff;color:var(--green);padding:0 10px}

/* hero */
.hero{position:absolute;left:0;top:139px;width:1200px;height:697px;background:linear-gradient(160deg,#c9d3d9 0%,#8c9ba6 45%,#5d6d78 75%,#7fae9e 100%)}
.hero h1{position:absolute;left:98px;top:141px;font-size:41px;font-weight:800;line-height:52px;text-transform:uppercase;color:#111}
.hero h1 span{color:var(--green)}
.hero p{position:absolute;left:104px;top:262px;width:700px;font-size:24px;line-height:30px;color:#111}
.hero .btn{left:98px;top:391px;width:158px;height:60px;font-size:20px;border:2px solid #a7d28a}
.dots{position:absolute;display:flex;gap:20px}
.dots i{width:18px;height:18px;border-radius:50%;background:#fff;display:block}
.dots i.on{background:transparent;border:2px solid #fff}
.badge{position:absolute;background:#1f3b96;border:4px solid #fff}

/* produkte */
.produkte{position:absolute;left:10px;top:893px;width:1190px;height:1022px;background:linear-gradient(180deg,#eef0f2,#e3e7ea)}
.sec-title{font-weight:800;color:var(--orange);text-transform:uppercase}
.produkte h2{position:absolute;left:0;width:1200px;top:30px;text-align:center;font-size:42px}
.produkte .lead{position:absolute;left:0;width:1200px;top:87px;text-align:center;font-size:20px;color:#333}
.card{position:absolute;width:488px;height:388px;overflow:hidden}
.card .band{position:absolute;left:0;width:488px;background:rgba(255,255,255,.9);text-align:center}
.card h3{font-size:30px;font-weight:800;color:var(--green);text-transform:uppercase}
.card small{font-size:16px;color:#222;display:block;margin-top:6px}
.card.green{background:linear-gradient(160deg,#8fc46b,#6aa844)}
.card.green h3{color:#fff;margin-top:44px;text-align:center}
.card.green small{color:#eaf4e1;text-align:center}
.card.green .btn{left:161px;top:268px;width:162px;height:62px;font-size:17px;border:3px solid #cfe7bf}

/* aktuelles */
.aktuelles{position:absolute;left:10px;top:1983px;width:1190px;height:537px;background:linear-gradient(180deg,#f1f3f4,#e4e8ea)}
.aktuelles h2{position:absolute;left:95px;top:92px;font-size:42px}
.aktuelles p{position:absolute;left:95px;top:192px;width:430px;font-size:17px;line-height:21px;color:#333}
.aktuelles .btn{left:95px;top:339px;width:156px;height:54px;font-size:20px}
.news-box{position:absolute;left:659px;top:175px;width:322px;height:113px;background:var(--green);color:#fff;font-weight:700;font-size:20px;display:flex;align-items:center;justify-content:center;text-align:center;line-height:26px}
.gdots{position:absolute;left:765px;top:487px;display:flex;gap:22px}
.gdots i{width:15px;height:15px;border-radius:50%;background:var(--green);display:block}
.gdots i.on{background:var(--orange)}

/* jobs */
.jobs{position:absolute;left:0;top:2571px;width:1200px;height:463px;background:linear-gradient(180deg,#eef0f1,#e6e9eb)}
.jobs h2{position:absolute;left:97px;top:35px;font-size:34px;font-weight:700;text-transform:uppercase;color:var(--orange)}
.jobs .intro{position:absolute;left:100px;top:90px;width:380px;font-size:17px;line-height:21px;color:#333}
.outline{position:absolute;left:97px;top:280px;width:364px;height:64px;border:3px solid var(--green);background:#fff;color:var(--green);font-weight:700;font-size:16px;display:flex;align-items:center;justify-content:center}
.jobs .list{left:98px;top:385px;width:365px;height:61px;font-size:15px;text-align:center;line-height:18px}
.job{position:absolute;top:90px;width:245px;height:352px;background:#fff;box-shadow:0 2px 6px rgba(0,0,0,.15);overflow:hidden}
.job .img{height:183px}
.job h4{font-size:16px;font-weight:800;color:var(--green);padding:14px 12px 0;text-transform:uppercase;line-height:18px}
.job p{font-size:10px;color:#555;padding:6px 12px 0;line-height:12px}
.tags{position:absolute;left:12px;bottom:14px;display:flex;gap:10px}
.tags span{background:#b5b5b5;color:#fff;font-size:12px;font-weight:600;border-radius:14px;padding:6px 9px}
.arrow-btn{position:absolute;top:2615px;width:22px;height:22px;background:var(--green)}

/* unternehmen */
.unternehmen{position:absolute;left:0;top:3088px;width:1200px;height:370px;background:linear-gradient(180deg,#8fc266 0%,#9cc479 40%,#7fa861 100%)}
.unternehmen h2{position:absolute;left:0;width:1200px;top:34px;text-align:center;color:#fff;font-size:36px;font-weight:800}
.unternehmen p{position:absolute;left:90px;width:1020px;top:116px;text-align:center;color:#fff;font-size:17px;font-weight:600;line-height:22px}
.unternehmen .btn{left:339px;top:243px;width:488px;height:54px;font-size:17px;border:3px solid #d9ecca}

/* formular */
.formular h2{position:absolute;left:98px;top:3518px;font-size:32px;font-weight:600;color:var(--orange)}
.hint{position:absolute;left:98px;top:3575px;font-size:14px;font-style:italic;color:#888;font-weight:300}
.lbl{position:absolute;font-size:14px;font-style:italic;color:#444}
.field{position:absolute;height:44px;border:1px solid #ddd;background:#fff;font-size:13px;color:#999;padding:0 12px;display:flex;align-items:center}
.field.focus{border:2px solid var(--green);color:#444;font-style:italic}
.send{left:98px;top:3853px;width:553px;height:51px;font-size:17px}
.map{position:absolute;left:683px;top:3517px;width:517px;height:382px;background:#e7e7e4}

/* footer */
.footer{position:absolute;left:0;top:3961px;width:1200px;height:406px;background:var(--footer)}
.footer .brand{left:97px;top:40px}
.footer .brand-name{font-size:44px}
.footer .brand-sub{color:#fff;font-size:20px}
.footer .rule{position:absolute;left:0;top:134px;width:1200px;height:6px;background:#3a3b3d}
.follow{position:absolute;left:119px;top:157px;color:#fff;font-size:20px;font-weight:600}
.soc{position:absolute;top:197px;width:40px;height:38px;background:var(--orange)}
.fc{position:absolute;display:flex;gap:16px;color:#fff;font-size:14px}
.fc .ic{width:32px;height:32px;border-radius:50%;background:var(--green);flex:none}
.fc b{display:block;font-weight:600;font-size:14px}
.fc em{font-style:normal;color:#bbb;font-size:13px}
.legal{position:absolute;left:97px;top:317px;display:flex;gap:28px;color:#fff;font-size:14px;font-weight:700}
</style>
</head>
<body>

<header>
  <div class="topbar">
    <div class="brand">
      <div class="brand-dot"></div>
      <div><div class="brand-name">KOLMATECH</div><div class="brand-sub">Maschinenbau GmbH</div></div>
    </div>
    <div class="contact" style="left:686px">
      <svg width="18" height="18" viewBox="0 0 24 24"><circle cx="12" cy="12" r="12" fill="#6cb33f"/><path d="M8 6l3 3-1.5 2a8 8 0 0 0 3.5 3.5l2-1.5 3 3-2 2C11 18 6 13 6 8z" fill="#fff"/></svg>
      030 555 / 210 - 0
    </div>
    <div class="contact" style="left:848px">
      <svg width="20" height="14" viewBox="0 0 20 14"><rect width="20" height="14" fill="#6cb33f"/><path d="M0 0l10 8 10-8" stroke="#fff" stroke-width="2" fill="none"/></svg>
      info@kolmatech.de
    </div>
    <div class="btn kontakt">Kontakt</div>
  </div>
  <nav class="nav">
    <a class="active">Unternehmen</a><a>Jobs &amp; Karriere</a><a>Palettiertechnik</a><a>Packertechnik</a><a>Fördertechnik</a><a>Anlagen</a><a>Gebrauchtmaschinen</a><a>Aktuelles</a>
  </nav>
</header>

<section class="hero" role="img" aria-label="Abfüllhalle mit geschwungenen Flaschen-Förderbändern">
  <h1>Fortschrittliche Verpackung<br>für die <span>moderne Industrie</span></h1>
  <p>Neueste Verpackungslösungen Für Hochwertige Lebensmittel Und Getränke, Effizienzsteigerung Und Ertragsoptimierung</p>
  <div class="btn">Mehr</div>
  <div class="dots" style="left:145px;top:520px"><i></i><i></i><i></i><i class="on"></i><i></i><i></i></div>
  <div class="badge" style="left:946px;top:420px;width:81px;height:119px"></div>
  <div class="badge" style="left:1037px;top:420px;width:81px;height:119px"></div>
</section>

<section class="produkte">
  <h2 class="sec-title">Unsere Produkte</h2>
  <div class="lead">Erfahren Sie Mehr Über Unsere Produkte. Wählen Sie Eine Kategorie:</div>

  <div class="card" style="left:100px;top:151px;background:linear-gradient(180deg,#6f7c86,#c4a77a)" role="img" aria-label="Palettieranlage mit Rollenbahn">
    <div class="band" style="top:143px;height:106px;padding-top:26px"><h3>Palettiertechnik</h3><small>StackLine Unsere Palettierfamilie</small></div>
  </div>
  <div class="card green" style="left:605px;top:151px" role="img" aria-label="Montagehalle mit Flaschenpacker, grün eingefärbt">
    <h3>Packertechnik</h3><small>PackLine Unsere Flaschenpacker</small>
    <div class="btn">Mehr dazu</div>
  </div>
  <div class="card" style="left:100px;top:570px;background:linear-gradient(180deg,#3e6b96,#c78a3c)" role="img" aria-label="Getränkeflaschen auf Transportband">
    <div class="band" style="top:143px;height:106px;padding-top:26px"><h3>Fördertechnik</h3><small>FlowLine Behälter- Und Gebindetransport</small></div>
  </div>
  <div class="card" style="left:605px;top:570px;background:linear-gradient(180deg,#a5683a,#5b4a3f)" role="img" aria-label="Industrieroboter in einer Fertigungshalle">
    <div class="band" style="top:143px;height:106px;padding-top:34px"><h3>Gebrauchtmaschinen</h3></div>
  </div>
</section>

<section class="aktuelles">
  <h2 class="sec-title">Aktuelles</h2>
  <p>Lorem Ipsum Is Simply Dummy Text Of The Printing And Typesetting Industry. Lorem Ipsum Has Been The Industry's Standard Dummy Text Ever Since The 1500s</p>
  <div class="btn">Mehr</div>
  <div class="ph" style="left:680px;top:8px;width:400px;height:420px;background:linear-gradient(160deg,#7f8b93,#b8c7d1);opacity:.8" role="img" aria-label="Abfüllanlage im Hintergrund"></div>
  <div class="ph" style="left:629px;top:59px;width:382px;height:333px;background:linear-gradient(160deg,#9fc97f,#7eb15a)" role="img" aria-label="Trockenteil einer Abfüllanlage, grün eingefärbt"></div>
  <div class="news-box">Neuer Trockenteil Bei<br>Quellhof Mineralbrunnen</div>
  <svg class="abs" style="left:565px;top:270px" width="100" height="140" viewBox="0 0 100 140"><path d="M90 135C45 125 20 80 20 30" stroke="#111" stroke-width="2.5" fill="none"/><path d="M10 40L20 25 30 40" stroke="#111" stroke-width="2.5" fill="none"/></svg>
  <svg class="abs" style="left:1085px;top:95px" width="50" height="115" viewBox="0 0 50 115"><path d="M20 110C45 80 45 35 5 10" stroke="#111" stroke-width="2.5" fill="none"/><path d="M3 25L5 8 20 12" stroke="#111" stroke-width="2.5" fill="none"/></svg>
  <div class="gdots"><i></i><i></i><i></i><i></i><i class="on"></i><i></i></div>
</section>

<section class="jobs">
  <h2>Jobs und Karriere</h2>
  <p class="intro">Schauen Sie sich jetzt unsere aktuellen Stellenangebote an und bewerben Sie sich ganz einfach auf Ihre Wunschstelle. Eine Bewerbung läuft ganz einfach in 60 Sekunden ab – ohne Lebenslauf oder Anschreiben.</p>
  <div class="outline">BEWERBEN</div>
  <div class="btn list">Hier kommen Sie zu den<br>Stellenanzeigen</div>

  <article class="job" style="left:508px">
    <div class="img" style="background:linear-gradient(160deg,#6a6a6a,#a34a3a)" role="img" aria-label="Technikerin an einer Steuerung"></div>
    <h4>SPS-Programmierung</h4>
    <p>Für Die Fertigung Unserer Einzel- Und Serienprodukte Im Bereich Getränkemaschinenbau Suchen Wir Eine Technisch Versierte Person</p>
    <div class="tags"><span>Vollzeit</span><span>Gehalt Verhandelbar</span></div>
  </article>
  <article class="job" style="left:771px">
    <div class="img" style="background:linear-gradient(160deg,#a7b3a0,#6f8c7a)" role="img" aria-label="Roboterzelle in der Fertigung"></div>
    <h4>Ausbildungsplätze für Mechatroniker</h4>
    <p>Für Die Fertigung Unserer Einzel- Und Serienprodukte Im Bereich Getränkemaschinenbau Bieten Folgende Ausbildungsplätze An</p>
    <div class="tags"><span>Vollzeit</span><span>Gehalt Verhandelbar</span></div>
  </article>
  <article class="job" style="left:1034px">
    <div class="img" style="background:linear-gradient(160deg,#c7ccd1,#e07a2a)" role="img" aria-label="Mitarbeiter mit Schutzhelm an einer Maschine"></div>
    <h4>Ausbildungsplätze Feinwerkmechanik</h4>
    <p>Für Die Fertigung Unserer Einzel- Und Serienprodukte Im Bereich Getränkemaschinenbau Bieten Ausbildungsplätze An</p>
    <div class="tags"><span>Vollzeit</span><span>Gehalt Verhandelbar</span></div>
  </article>
</section>
<svg class="abs" style="left:1114px;top:2614px" width="22" height="22" viewBox="0 0 22 22"><rect width="22" height="22" fill="#6cb33f"/><path d="M14 5L7 11l7 6z" fill="#fff"/></svg>
<svg class="abs" style="left:1158px;top:2614px" width="22" height="22" viewBox="0 0 22 22"><rect width="22" height="22" fill="#6cb33f"/><path d="M8 5l7 6-7 6z" fill="#fff"/></svg>

<section class="unternehmen" role="img" aria-label="Firmengelände mit Werkshalle, grün eingefärbt">
  <h2>UNTERNEHMEN</h2>
  <p>Das Traditionsreiche Familienunternehmen Kolmatech Plant, Entwickelt Und Baut Pack- Und Palettieranlagen Für Den Getränke- Und Lebensmittelbereich. Mit Erfahrung Und Know-How Planen Und Konstruieren Wir Moderne Und Leistungsfähige Anlagen, Die Optimal Auf Die Bedürfnisse Unserer Kunden Abgestimmt Sind.</p>
  <div class="btn">Hier können Sie mehr über uns erfahren</div>
</section>

<section class="formular">
  <h2>Rückruf-Formular</h2>
  <div class="hint">gewünschter Rückruf-Zeitpunkt</div>
  <div class="lbl" style="left:102px;top:3597px">Vorname</div>
  <div class="field" style="left:98px;top:3622px;width:264px">Enter your &nbsp;Vorname</div>
  <div class="lbl" style="left:389px;top:3597px">Nachname</div>
  <div class="field" style="left:389px;top:3622px;width:262px">Enter your nachname</div>
  <div class="lbl" style="left:98px;top:3671px">Mail</div>
  <div class="field focus" style="left:98px;top:3695px;width:264px">john.exp@gm</div>
  <div class="lbl" style="left:389px;top:3671px">Telefon</div>
  <div class="field" style="left:389px;top:3695px;width:262px">telefon</div>
  <div class="lbl" style="left:98px;top:3744px">Kommentar</div>
  <div class="field" style="left:98px;top:3768px;width:553px;height:68px;align-items:flex-start;padding-top:14px">Kommentar</div>
  <div class="btn send">Senden</div>
  <div class="map" role="img" aria-label="Lageplan des Firmenstandorts im Gewerbegebiet"></div>
</section>

<footer class="footer">
  <div class="brand">
    <div class="brand-dot" style="width:46px;height:46px"></div>
    <div><div class="brand-name">KOLMATECH</div><div class="brand-sub">Maschinenbau GmbH</div></div>
  </div>
  <div class="abs" style="left:690px;top:41px;width:236px;height:66px;background:#fff"></div>
  <div class="abs" style="left:700px;top:49px;width:92px;height:50px;background:#1f3b96"></div>
  <div class="abs" style="left:946px;top:41px;width:159px;height:66px;background:#fff"></div>
  <div class="abs" style="left:956px;top:49px;width:139px;height:50px;background:#1f3b96"></div>
  <div class="rule"></div>
  <div class="follow">Folgen Sie Uns</div>
  <div class="soc" style="left:115px"></div>
  <div class="soc" style="left:175px"></div>
  <div class="soc" style="left:235px"></div>
  <div class="soc" style="left:295px"></div>

  <div class="fc" style="left:532px;top:153px"><svg class="ic" viewBox="0 0 32 32"><circle cx="16" cy="16" r="16" fill="#6cb33f"/><rect x="9" y="11" width="14" height="10" fill="#fff"/><path d="M9 11l7 6 7-6" stroke="#6cb33f" fill="none"/></svg><div><em>Email</em><b>Info@Kolmatech.De</b></div></div>
  <div class="fc" style="left:532px;top:213px"><svg class="ic" viewBox="0 0 32 32"><circle cx="16" cy="16" r="16" fill="#6cb33f"/><path d="M11 9l4 4-2 2.5a10 10 0 0 0 4.5 4.5l2.5-2 4 4-2.5 2.5C14 24 8 18 8.5 11.5z" fill="#fff"/></svg><div><em>Telefon</em><b>030 555 / 210 - 0</b></div></div>
  <div class="fc" style="left:797px;top:153px"><svg class="ic" viewBox="0 0 32 32"><circle cx="16" cy="16" r="16" fill="#6cb33f"/><rect x="10" y="12" width="12" height="10" fill="#fff"/><rect x="12" y="8" width="8" height="5" fill="#fff"/></svg><div><em>Fax</em><b>030 555 / 210 - 0</b></div></div>
  <div class="fc" style="left:797px;top:213px"><svg class="ic" viewBox="0 0 32 32"><circle cx="16" cy="16" r="16" fill="#6cb33f"/><path d="M16 7a6 6 0 0 0-6 6c0 5 6 12 6 12s6-7 6-12a6 6 0 0 0-6-6z" fill="#fff"/><circle cx="16" cy="13" r="2" fill="#6cb33f"/></svg><div><em>Standort</em><b>KOLMATECH Maschinenbau GmbH<br>Werkstraße 5 04700 Musterstadt</b></div></div>

  <div class="legal"><span>2024 © KOLMATECH Maschinenbau GmbH</span><span>Palettiertechnik</span><span>Packertechnik</span><span>Fördertechnik</span><span>Anlagen</span><span>Gebrauchtmaschinen</span><span>Aktuelles</span></div>
</footer>

</body>
</html>
```